Bramblewick Forage Business Cards

I need a business card with my logo, number, Facebook account, and some information about what I am selling. Green card with logo on the front. 555-214-8392 phone number, @bramblewickforage Facebook, •Orchardgrass Hay •Alfalfa Hay •Mixed Grass Hay , and “Premium Quality Hay” all written on the back.

Target Market(s)

Hay

Contact Information for Business Card

Phone number, Facebook, different types of hay.

Colors
00AB8E
00BBA5
67D7C9
C6EFE9
E9F9F6

```html
<!DOCTYPE html>
<html lang="en">
<head>
<meta charset="utf-8">
<title>Bramblewick Forage Business Cards</title>
<link rel="stylesheet" href="https://fonts.googleapis.com/css2?family=Arimo:wght@400;700&display=swap">
<style>
  :root {
    --page: #d4d4d4;
    --card-white: #ffffff;
    --brand-green: #00a651;
    --brand-green-dark: #008c43;
    --brand-green-light: #2fd07a;
    --ink: #111111;
    --rule-grey: #c8c8c8;
  }
  * { box-sizing: border-box; margin: 0; padding: 0; }
  html, body {
    width: 1200px; height: 800px; overflow: hidden;
    background: var(--page);
    font-family: "Arimo", Arial, sans-serif;
  }
  .sheet {
    width: 1200px; height: 800px;
    display: flex; align-items: center; justify-content: center; gap: 40px;
  }
  .card {
    position: relative;
    width: 560px; height: 320px;
    overflow: hidden;
    box-shadow: 0 8px 22px rgba(0,0,0,.22);
  }

  /* Info side */
  .card--info { background: var(--card-white); border-bottom: 3px solid var(--brand-green); }
  .brand-lockup {
    position: absolute; top: 52px; left: 0; right: 0;
    display: flex; align-items: center; justify-content: center; gap: 22px;
  }
  .brand-dot { width: 46px; height: 46px; border-radius: 50%; background: var(--brand-green); }
  .brand-divider { width: 1px; height: 60px; background: var(--rule-grey); }
  .brand-name { font-weight: 700; font-size: 32px; color: var(--ink); letter-spacing: .2px; }

  .contact-row {
    position: absolute; top: 150px; left: 44px; right: 44px;
    display: flex; justify-content: space-between; align-items: center;
  }
  .contact-item { display: flex; align-items: center; gap: 10px; font-size: 17px; color: var(--ink); }
  .contact-icon {
    width: 30px; height: 30px; border-radius: 50%;
    background: var(--brand-green);
    display: flex; align-items: center; justify-content: center;
  }
  .green-rule {
    position: absolute; top: 200px; left: 44px; right: 44px;
    height: 1.5px; background: var(--brand-green);
  }
  .hay-list {
    position: absolute; top: 222px; left: 52px; right: 44px;
    list-style: none;
    display: grid; grid-template-columns: 1fr 1fr; row-gap: 12px; column-gap: 24px;
    font-size: 17px; color: var(--ink);
  }
  .hay-list li { display: flex; align-items: center; gap: 9px; }
  .hay-list li::before {
    content: ""; width: 9px; height: 9px; border-radius: 50%; background: var(--brand-green);
  }

  /* Logo side */
  .card--logo { background: var(--brand-green); }
  .leaf-pattern {
    position: absolute; inset: 0;
    background: linear-gradient(150deg, var(--brand-green-light) 0%, var(--brand-green) 45%, var(--brand-green-dark) 100%);
    opacity: .85;
  }
  .front-lockup {
    position: absolute; left: 0; right: 0; top: 142px;
    display: flex; align-items: center; justify-content: center; gap: 16px;
  }
  .front-dot { width: 40px; height: 40px; border-radius: 50%; background: var(--card-white); }
  .front-name { font-weight: 700; font-size: 32px; color: var(--ink); }
</style>
</head>
<body>
<main class="sheet">

  <section class="card card--info" aria-label="Card back with contact details">
    <div class="brand-lockup">
      <span class="brand-dot"></span>
      <span class="brand-divider"></span>
      <span class="brand-name">Bramblewick Forage</span>
    </div>

    <div class="contact-row">
      <div class="contact-item">
        <span class="contact-icon">
          <svg width="16" height="16" viewBox="0 0 24 24" aria-hidden="true">
            <path fill="#fff" d="M6.6 10.8a15.1 15.1 0 0 0 6.6 6.6l2.2-2.2a1 1 0 0 1 1-.25 11.4 11.4 0 0 0 3.6.57 1 1 0 0 1 1 1V20a1 1 0 0 1-1 1A17 17 0 0 1 3 4a1 1 0 0 1 1-1h3.5a1 1 0 0 1 1 1c0 1.25.2 2.45.57 3.57a1 1 0 0 1-.25 1z"/>
          </svg>
        </span>
        <span class="contact-text">555-214-8392</span>
      </div>
      <div class="contact-item">
        <span class="contact-icon"></span>
        <span class="contact-text">@bramblewickforage</span>
      </div>
    </div>

    <div class="green-rule"></div>

    <ul class="hay-list">
      <li>Orchardgrass Hay</li>
      <li>Alfalfa Hay</li>
      <li>Mixed Grass Hay</li>
      <li>Premium Quality Hay</li>
    </ul>
  </section>

  <section class="card card--logo" aria-label="Card front with brand name">
    <div class="leaf-pattern" role="img" aria-label="Repeating pattern of green leaf emblems across the card"></div>
    <div class="front-lockup">
      <span class="front-dot"></span>
      <span class="front-name">Bramblewick Forage</span>
    </div>
  </section>

</main>
</body>
</html>
```